Quiet Porch Podcast Cover Graphic

We need a graphic designed for a new podcast called "Quiet Porch." The graphic will be used on multiple podcasting platforms as the lead graphic advertising the podcast. The podcast consists of interviews of individuals sharing their life experiences including challenges, successes, lessons learned, and unexpected turns. The purpose of the podcast is to help listeners and participants learn from the life experiences of everyday neighbors. This podcast has a heavy Christian foundation on the parable of the good samaritan. We believe that through hearing the experiences of everyday neighbors, listeners can be strengthened, nourished, and aided to handle their own life challenges and trials. We would like the final design to be simple and reflective of the purpose and the parable of the good samaritan. The final design needs to have the title of the podcast, "Quiet Porch." We believe the best designs will limit the number of colors to less than 5 and will look good in a monochromatic version as well as a color version. We think the color white should be the main color. The graphic should be square in dimensions. We have considered having two hands grasping each other as if to lift the hand from below, but open to other creative simple takes to convey the lessons from the good samaritan.

```html
<!DOCTYPE html>
<html lang="en">
<head>
<meta charset="utf-8">
<title>Quiet Porch Podcast Cover</title>
<link rel="stylesheet" href="https://fonts.googleapis.com/css2?family=Montserrat:wght@300;400&display=swap">
<style>
  :root {
    --stage: #d6d6d4;
    --paper: #e9e8e0;
    --band-red: #e52b1d;
    --ladder-red: #c8261a;
    --strip-white: #ffffff;
    --ink: #141414;
    --figure-ink: #2a2a2a;
  }
  html, body {
    margin: 0;
    padding: 0;
    width: 1200px;
    height: 2168px;
    overflow: hidden;
    background: var(--stage);
  }
  .canvas {
    position: relative;
    width: 1200px;
    height: 2168px;
    display: flex;
    align-items: center;
    justify-content: center;
  }
  .cover {
    width: 1080px;
    height: 1080px;
    display: block;
  }
  .cover-paper { fill: var(--paper); }
  .cover-strip { fill: var(--strip-white); }
  .cover-band { fill: var(--band-red); }
  .cover-title {
    font-family: "Montserrat", sans-serif;
    font-weight: 300;
    font-size: 120px;
    fill: var(--ink);
    text-anchor: middle;
  }
  .cover-label {
    font-family: "Montserrat", sans-serif;
    font-weight: 300;
    font-size: 38px;
    letter-spacing: 22px;
    fill: var(--band-red);
    text-anchor: middle;
  }
  .figure-area { fill: var(--figure-ink); }
  .ladder-area { fill: var(--ladder-red); }
</style>
</head>
<body>
  <main class="canvas">
    <svg class="cover" viewBox="0 0 793 793" xmlns="http://www.w3.org/2000/svg" aria-labelledby="cover-name">
      <title id="cover-name">Quiet Porch Podcast</title>
      <rect class="cover-paper" x="0" y="0" width="793" height="793"/>

      <text class="cover-title" x="396" y="181">QUIET</text>
      <text class="cover-title" x="396" y="291">PORCH</text>

      <polygon class="cover-strip" points="0,376 793,466 793,491 0,392"/>
      <polygon class="cover-band" points="0,392 793,491 793,749 0,501"/>

      <rect class="figure-area" x="364" y="364" width="22" height="68" role="img"
            aria-label="Small silhouette of a person standing on the ledge, casting a long shadow"/>
      <rect class="ladder-area" x="301" y="456" width="155" height="190" role="img"
            aria-label="Red ladder leaning against the wall below the ledge, with its shadow on the ground"/>

      <text class="cover-label" x="407" y="752">PODCAST</text>
    </svg>
  </main>
</body>
</html>
```